Weightloss company needs Business Card

We want a business card that is clean and professional, yet portrays that we are a friendly, innovative, and versatile program designed to fit the needs of our clients.
I would like there to be 2 sides, one side having an appointment card, and the other side containing the logo and business information. There can be decorations on both sides. The logo is attached.

Target Market(s)

Men and women 40-60

Industry/Entity Type

Business

Contact Information for Business Card

Font styles to use
Sans Serif

Requirements
Must have
• The logo, space for business information
Nice to have
• The colors in the logo
Should not have
• No pictures of people or food

```html
<!DOCTYPE html>
<html lang="en">
<head>
<meta charset="utf-8">
<title>Renew Turn Wellness – Business Card</title>
<link href="https://fonts.googleapis.com/css2?family=Open+Sans:wght@400;600;700&display=swap" rel="stylesheet">
<style>
  :root {
    --brand-red: #e3263a;
    --brand-blue: #3bbfe8;
    --card-black: #0c0c0d;
    --card-white: #ffffff;
    --ink: #1c1c1c;
    --line-grey: #8a8a8a;
    --page-bg: #e9e9eb;
  }
  * { margin: 0; padding: 0; box-sizing: border-box; }
  html, body {
    width: 1200px; height: 900px; overflow: hidden;
    background: var(--page-bg);
    font-family: "Open Sans", Arial, sans-serif;
  }
  .card {
    position: absolute; left: 290px;
    width: 620px; height: 354px;
    border-radius: 22px; overflow: hidden;
    box-shadow: 0 6px 18px rgba(0,0,0,.18);
  }

  /* Appointment side */
  .appointment-card { top: 70px; background: var(--card-white); }
  .appointment-title {
    position: absolute; left: 46px; top: 96px;
    color: var(--brand-red); font-size: 15px; letter-spacing: .5px;
  }
  .appointment-field {
    position: absolute; left: 66px;
    display: flex; align-items: flex-end; gap: 10px;
    color: var(--ink); font-size: 15px;
  }
  .appointment-field .rule { height: 1px; background: var(--ink); margin-bottom: 5px; }
  .field-name { top: 140px; } .field-name .rule { width: 290px; }
  .field-date { top: 192px; left: 92px; } .field-date .rule { width: 270px; }
  .field-time { top: 244px; left: 118px; } .field-time .rule { width: 250px; }
  .appointment-brand {
    position: absolute; right: 40px; top: 150px;
    display: flex; align-items: center; gap: 10px;
    color: var(--brand-red); font-weight: 700; font-size: 26px; line-height: 1;
  }
  .brand-dot { width: 14px; height: 14px; border-radius: 50%; background: var(--brand-blue); }

  /* Info side */
  .info-card { top: 476px; background: var(--card-black); }
  .info-rule {
    position: absolute; left: 250px; right: 40px; top: 96px;
    height: 1px; background: var(--line-grey);
  }
  .person-name {
    position: absolute; left: 36px; top: 74px;
    color: var(--brand-red); font-size: 21px; letter-spacing: .5px;
  }
  .person-title {
    position: absolute; left: 38px; top: 104px;
    color: var(--brand-blue); font-size: 13px; letter-spacing: .5px;
  }
  .info-brand {
    position: absolute; right: 44px; top: 140px;
    display: flex; align-items: center; gap: 10px;
    color: var(--brand-red); font-weight: 700; font-size: 28px; line-height: 1;
  }
  .info-band {
    position: absolute; left: 330px; right: 0; top: 212px; bottom: 0;
    background: var(--card-white);
    border-top-left-radius: 80px;
  }
  .band-edge {
    position: absolute; left: 318px; top: 206px;
  }
  .address {
    position: absolute; right: 26px; top: 222px; text-align: right;
    color: var(--brand-blue); font-size: 13px; line-height: 1.45;
  }
  .contact-list {
    position: absolute; left: 36px; bottom: 30px;
    list-style: none; color: var(--card-white); font-size: 14px; line-height: 1.7;
  }
  .contact-list li { display: flex; align-items: center; gap: 12px; }
  .contact-list svg { width: 13px; height: 13px; flex: none; }
</style>
</head>
<body>

<section class="card appointment-card">
  <p class="appointment-title">APPOINTMENT</p>
  <div class="appointment-field field-name"><span>Name:</span><span class="rule"></span></div>
  <div class="appointment-field field-date"><span>Date:</span><span class="rule"></span></div>
  <div class="appointment-field field-time"><span>Time:</span><span class="rule"></span></div>
  <div class="appointment-brand"><span class="brand-dot"></span><span>Renew Turn<br>Wellness</span></div>
</section>

<section class="card info-card">
  <span class="info-rule"></span>
  <p class="person-name">MARCUS ELLERY</p>
  <p class="person-title">DIRECTOR</p>
  <div class="info-brand"><span class="brand-dot"></span><span>Renew Turn<br>Wellness</span></div>

  <div class="info-band"></div>
  <svg class="band-edge" width="120" height="150" viewBox="0 0 120 150" aria-hidden="true">
    <path d="M100 6 A 90 90 0 0 0 12 96 L12 150" fill="none" stroke="var(--brand-red)" stroke-width="4"/>
  </svg>
  <p class="address">Cedar Avenue, 40218<br>Northfield, Aldoria</p>

  <ul class="contact-list">
    <li>
      <svg viewBox="0 0 24 24"><path fill="var(--brand-red)" d="M6.6 10.8a15 15 0 0 0 6.6 6.6l2.2-2.2c.3-.3.7-.4 1-.2 1.1.4 2.3.6 3.6.6.6 0 1 .4 1 1V20c0 .6-.4 1-1 1A17 17 0 0 1 3 4c0-.6.4-1 1-1h3.5c.6 0 1 .4 1 1 0 1.3.2 2.5.6 3.6.1.3 0 .7-.2 1z"/></svg>
      <span>+330 5512-7408</span>
    </li>
    <li>
      <svg viewBox="0 0 24 24"><rect x="2" y="5" width="20" height="14" rx="2" fill="none" stroke="var(--brand-red)" stroke-width="2"/><path d="M3 6l9 7 9-7" fill="none" stroke="var(--brand-red)" stroke-width="2"/></svg>
      <span>hello@renewturnwellness.com</span>
    </li>
    <li>
      <svg viewBox="0 0 24 24"><circle cx="12" cy="12" r="10" fill="var(--brand-red)"/><path d="M2 12h20M12 2c3 3 3 17 0 20M12 2c-3 3-3 17 0 20" fill="none" stroke="var(--card-black)" stroke-width="1.5"/></svg>
      <span>www.renewturnwellness.com</span>
    </li>
  </ul>
</section>

</body>
</html>
```